ORLA - Óptica Médica - web design and concept

Website concept - Create and develop our website design and structure. ORLA is an optical store chain, and we are looking to establish our web and digital concept. In attachment there are several pictures about our stores and our logo.

The website structure should be user friendly. Colors should be light and the design as simple and minimalist as possible. There are different variations of the logothat can be used, check the file.

The website will include optical collections and sun collections as an online store. Also, a medical menu should be considered in order for clients to schedule optometry appointments. There should also be a menu for client assistance where the clients can read about glass maintenance in our workshop.
Updates

Low design quality

Number of Pages Required

5+ page

Font styles to use
Serif
Sans Serif

Requirements
Must have
• Must be user-friendly and minimalist.
• Please USE PICTURES FROM THE BRANDS we sell: MERUN, BOSKA, PNW, KOLE, BAMPE
Nice to have
• Nice to inspire: ZEK glasses (see website https://ch.shopzek.com/en/)
• Nice to inspire: https://merun-eyewear.com/
• Nice to ispire: https://www.pnwglobe.com/en/
Should not have
• Hysteric colors and shapes

```html
<!DOCTYPE html>
<html lang="en">
<head>
<meta charset="utf-8">
<title>ORLA – Contact Us</title>
<link href="https://fonts.googleapis.com/css2?family=Heebo:wght@300&family=Lato:wght@400;700&display=swap" rel="stylesheet">
<style>
:root{
  --gold:#ebb55c;
  --ink:#222;
  --text:#444;
  --muted:#666;
  --line:#e4e4e4;
  --paper:#fff;
  --night:#000;
}
*{margin:0;padding:0;box-sizing:border-box}
html,body{width:793px;height:1200px;overflow:hidden;background:var(--paper)}
body{position:relative;font-family:"Lato",sans-serif;color:var(--text);font-size:7.5px}
.abs{position:absolute}
.social{display:flex;gap:6px}
.social span{width:7px;height:7px;border-radius:50%;background:var(--ink);display:block}
.site-header .social{left:108px;top:11px}
.brand{left:0;width:793px;top:24px;text-align:center;font-family:"Lato",sans-serif;font-size:16px;letter-spacing:3px;color:var(--ink)}
.cart{left:542px;top:10px;display:flex;align-items:center;gap:4px;color:var(--text)}
.phone-top{left:619px;top:9px;display:flex;align-items:center;gap:4px}
.nav{left:310px;top:69px;display:flex;align-items:center;gap:13px;color:var(--ink)}
.nav .active{color:var(--gold)}
.nav .cta{background:var(--gold);border:1px solid #d9a44e;padding:2px 7px;margin-left:-4px}
.page-title,.form-title{left:0;width:793px;text-align:center;font-family:"Heebo",sans-serif;font-weight:300;font-size:30px;color:var(--night)}
.page-title{top:137px}
.form-title{top:238px}
.label{font-size:7px;color:var(--text)}
.field{border:1px solid var(--line);background:var(--paper)}
.send{left:109px;top:710px;width:121px;height:35px;background:var(--gold);color:var(--ink);font-size:9px;display:flex;align-items:center;justify-content:center;letter-spacing:.2px}
.info h2{font-family:"Heebo",sans-serif;font-weight:300;font-size:18px;color:var(--ink);margin-bottom:4px}
.info p{font-size:7.2px;line-height:15px;color:var(--text);padding-left:2px}
.site-footer{left:0;top:983px;width:793px;height:217px;background:var(--night);color:#fff}
.footer-brand{left:106px;top:37px;font-size:12px;letter-spacing:2px;color:var(--gold)}
.footer-about{left:106px;top:76px;width:102px;font-size:7px;line-height:9px}
.footer-more{left:106px;top:108px;font-size:7px}
.site-footer .social{left:106px;top:127px}
.site-footer .social span{background:var(--gold)}
.col h3{font-size:8.5px;font-weight:700;color:var(--gold);margin-bottom:13px}
.col ul{list-style:none}
.col li{font-size:7px;line-height:11px;padding-left:9px;position:relative}
.col li::before{content:"";position:absolute;left:0;top:4.5px;width:2.5px;height:2.5px;border-radius:50%;background:var(--gold)}
.contact-list li{padding-left:10px;line-height:11px;margin-bottom:5px}
.contact-list li::before{display:none}
.contact-list svg{position:absolute;left:0;top:2px}
.divider{left:106px;top:149px;width:582px;height:1px;background:#888}
.copyright{left:107px;top:159px;font-size:8.5px}
.legal{left:520px;width:168px;top:155px;text-align:right;font-size:8.5px}
</style>
</head>
<body>
<header class="site-header">
  <div class="social abs" aria-label="Social links"><span></span><span></span><span></span><span></span><span></span></div>
  <div class="brand abs">ORLA</div>
  <div class="cart abs">
    <svg width="7" height="8" viewBox="0 0 7 8"><path d="M2 3V2a1.5 1.5 0 0 1 3 0v1" fill="none" stroke="#222"/><rect x="0.5" y="3" width="6" height="5" fill="#222"/></svg>
    Your Cart &nbsp;( 0 )
  </div>
  <div class="phone-top abs">
    <svg width="7" height="7" viewBox="0 0 10 10"><path d="M2 0l2 2.5-1.2 1.2a6 6 0 0 0 3.5 3.5L7.5 6 10 8l-1.5 2C4 10 0 6 0 1.5z" fill="#222"/></svg>
    +012-555-410-2
  </div>
  <nav class="nav abs">
    <span>Home</span><span>Sun</span><span>Optical</span><span>Store</span>
    <span class="active">Contact Us</span><span class="cta">Make an Appoinment</span>
  </nav>
</header>

<main>
  <h1 class="page-title abs">Contact Us</h1>
  <h2 class="form-title abs">Send Us Your Feedback</h2>

  <div class="label abs" style="left:108px;top:284px">Name</div>
  <div class="field abs" style="left:107px;top:299px;width:581px;height:46px"></div>
  <div class="label abs" style="left:108px;top:364px">E-Mail Address</div>
  <div class="field abs" style="left:107px;top:379px;width:581px;height:45px"></div>
  <div class="label abs" style="left:108px;top:444px">Subject</div>
  <div class="field abs" style="left:107px;top:458px;width:285px;height:45px"></div>
  <div class="label abs" style="left:401px;top:444px">Phone Number</div>
  <div class="field abs" style="left:401px;top:458px;width:285px;height:45px"></div>
  <div class="label abs" style="left:108px;top:522px">Massage</div>
  <div class="field abs" style="left:107px;top:536px;width:581px;height:148px"></div>
  <div class="send abs">SEND MASSAGE</div>

  <section class="info abs" style="left:106px;top:834px">
    <h2>Call Us</h2>
    <p>Telephone &nbsp;: +012-555-410-7<br>Mobile &nbsp;: +012-555-410-7</p>
  </section>
  <section class="info abs" style="left:337px;top:834px">
    <h2>Mail Us</h2>
    <p>E-Mail &nbsp;: hello@orlaoptica.com</p>
  </section>
  <section class="info abs" style="left:556px;top:834px">
    <h2>Opening Hours</h2>
    <p>Monday – 3:00pm – 7:30pm<br>Tuesday – Saturday<br>10:00am – 1:00pm &nbsp;&nbsp;3:00pm – 7:30pm<br>[Friday closed]</p>
  </section>
</main>

<footer class="site-footer abs">
  <div class="footer-brand abs">ORLA</div>
  <p class="footer-about abs">Lorem Ipsum is simply dummy text of the printing and typesetting industry.</p>
  <div class="footer-more abs">READ MORE....</div>
  <div class="social abs"><span></span><span></span><span></span><span></span><span></span></div>

  <div class="col abs" style="left:279px;top:58px">
    <h3>QUICK LINK</h3>
    <ul><li>Women</li><li>Men</li><li>Youth</li><li>Collections</li><li>Contact Us</li></ul>
  </div>
  <div class="col abs" style="left:420px;top:58px">
    <h3>ACCOUNT</h3>
    <ul><li>My Account</li><li>My Wishlist</li><li>Checkout</li><li>Create Account</li><li>Register</li></ul>
  </div>
  <div class="col abs" style="left:567px;top:58px">
    <h3>QUICK CONTACT</h3>
    <ul class="contact-list">
      <li><svg width="6" height="6" viewBox="0 0 10 10"><path d="M2 0l2 2.5-1.2 1.2a6 6 0 0 0 3.5 3.5L7.5 6 10 8l-1.5 2C4 10 0 6 0 1.5z" fill="#ebb55c"/></svg>+012-555-410-7</li>
      <li><svg width="7" height="5" viewBox="0 0 7 5"><rect width="7" height="5" fill="#ebb55c"/><path d="M0 0l3.5 2.5L7 0" fill="none" stroke="#000" stroke-width=".6"/></svg>hello@orlaoptica.com</li>
      <li><svg width="5" height="7" viewBox="0 0 10 14"><path d="M5 0a5 5 0 0 1 5 5c0 4-5 9-5 9S0 9 0 5a5 5 0 0 1 5-5z" fill="#ebb55c"/><circle cx="5" cy="5" r="2" fill="#000"/></svg>14 Linden Row<br>Brookfield, OR 97120</li>
    </ul>
  </div>

  <div class="divider abs"></div>
  <div class="copyright abs">CopyRight &nbsp;©2018 Orla Óptica Médica. All Right Reserve</div>
  <div class="legal abs">Privacy Policy - Terms &amp; Conditions</div>
</footer>
</body>
</html>
```